Business card for law firm

Need business card for new law firm. Think confident, authoritative, conservative, but not stuffy or old-fashioned.

Contact Information for Business Card

Content for card - logo (uploaded), plus the following:

Paul Whitcombe (larger font)
Managing Partner (larger font, but not as large as name)
Level 9, 7 Ferris Lane
Sydney NSW 2000
Main Tel 02 9364 2710
Direct Tel 02 8472 3159
Email paul@qvlegal.com.au
www.qvlegal.com.au

Letterhead design should include logo plus:
Level 9, 7 Ferris Lane
Sydney NSW 2000
Tel 02 8472 3159
www.qvlegal.com.au

```html
<!DOCTYPE html>
<html lang="en">
<head>
<meta charset="utf-8">
<title>Quayvale Lawyers – Business Card</title>
<link href="https://fonts.googleapis.com/css2?family=Open+Sans:wght@400;600&family=Roboto:wght@500;700&display=swap" rel="stylesheet">
<style>
  :root {
    --navy: #0b1b55;
    --paper: #ffffff;
    --ink: #4a4a4a;
    --stage: #dcdcdc;
  }
  * { margin: 0; padding: 0; box-sizing: border-box; }
  html, body {
    width: 1146px;
    height: 1200px;
    overflow: hidden;
    background: var(--stage);
  }
  .sheet { position: relative; width: 1146px; height: 1200px; }

  .card {
    position: absolute;
    left: 206px;
    width: 731px;
    height: 421px;
    overflow: hidden;
  }
  .card--front { top: 125px; background: var(--paper); }
  .card--back { top: 654px; background: var(--navy); }

  .card__band {
    position: absolute;
    left: 0; right: 0; bottom: 0;
    height: 12px;
    background: var(--navy);
  }

  .brand {
    position: absolute;
    display: flex;
    flex-direction: column;
    align-items: center;
    gap: 22px;
  }
  .card--front .brand { left: 38px; width: 380px; top: 122px; }
  .card--back .brand { left: 0; right: 0; top: 140px; }

  .brand__mark { width: 46px; height: 46px; background: var(--navy); }
  .card--back .brand__mark { background: var(--paper); }

  .brand__name {
    font-family: "Roboto", sans-serif;
    font-weight: 500;
    font-size: 30px;
    letter-spacing: 4px;
    color: var(--navy);
    text-transform: uppercase;
  }
  .card--back .brand__name { color: var(--paper); font-size: 34px; }

  .contact {
    position: absolute;
    left: 416px;
    top: 94px;
    font-family: "Open Sans", sans-serif;
    color: var(--ink);
  }
  .contact__name {
    font-family: "Roboto", sans-serif;
    font-weight: 700;
    font-size: 35px;
    line-height: 40px;
    color: var(--navy);
  }
  .contact__role {
    font-family: "Roboto", sans-serif;
    font-weight: 500;
    font-size: 21px;
    line-height: 24px;
    color: #111;
  }
  .contact__lines {
    font-size: 16.5px;
    line-height: 21.5px;
    margin-top: 18px;
  }
  .contact__lines + .contact__lines { margin-top: 12px; }
  .contact__web {
    font-weight: 600;
    font-size: 17px;
    margin-top: 14px;
  }
</style>
</head>
<body>
<main class="sheet">
  <section class="card card--front">
    <div class="brand">
      <span class="brand__mark"></span>
      <span class="brand__name">Quayvale Lawyers</span>
    </div>
    <div class="contact">
      <p class="contact__name">Paul Whitcombe</p>
      <p class="contact__role">Managing Partner</p>
      <p class="contact__lines">Level 9, 7 Ferris Lane<br>Sydney NSW 2000</p>
      <p class="contact__lines">02 9364 2710 (Main)<br>02 8472 3159 (Direct)<br>paul@qvlegal.com.au</p>
      <p class="contact__web">www.qvlegal.com.au</p>
    </div>
    <div class="card__band"></div>
  </section>

  <section class="card card--back">
    <div class="brand">
      <span class="brand__mark"></span>
      <span class="brand__name">Quayvale Lawyers</span>
    </div>
  </section>
</main>
</body>
</html>
```